Roadside building business signage for a holistic health clinic.

Replace signs as shown in the attached file. They are perforated stickers that go on the windows as shown. Looking for something that has our logo and says the name of the practice with logo (Fernridge Health & Wellness) also boldly says Acupuncture, IV Vitamins, and Holistic Health.
Possibly our phone number as well 318-562-7041
Updates

Please don't use pink except the logo. Earthy, organic tone colors appreciated.

Need of eye catching window signage of a holistic clinic on a brick building. Pink, purple, sage green, white color. Logo is pink on a white background. Please don't overload with too much pink. Words to include are "Fernridge Health and Wellness(name of business)", "Direct Primary Care", " Medical acupuncture", "IV Vitamin Therapy", "fernridgecareclinic.example","318-562-7041".

Target Market(s)

People will see in their cars passing by the building. Busy roadside so need to be visible while passing in fast speed.

Industry/Entity Type

Health & Wellness

Font styles to use
Sans Serif

Colors

Designer to choose colors to be used in the design.

Requirements
Must have
• On sign must have words Holistic Medicine, Medical Acupuncture, Direct Primary Care and IV vitamins.
Nice to have
• Simple, minimalistic, artistic yet has clear message. White, Black, Violet, Pink (logo), Dark green, Sage green.
Should not have
• Bold colors (red, yellow, blue), same tone colors. Blue waves on the current signage (uploaded file) must go.

```html
<!DOCTYPE html>
<html lang="en">
<head>
<meta charset="utf-8">
<title>Fernridge Health &amp; Wellness — Window Signage</title>
<link href="https://fonts.googleapis.com/css2?family=Dosis:wght@500;600&display=swap" rel="stylesheet">
<style>
  :root {
    --backdrop: #000000;
    --cream: #f4efe2;
    --white: #ffffff;
    --forest: #1f5a40;
    --forest-deep: #2f6a52;
    --sage: #7f9a86;
    --blush: #f0b7a4;
    --pond-dark: #2b3a2a;
    --pond-mid: #5d7a47;
    --lotus-pink: #e0448e;
    --mauve: #b0768e;
    --ink: #1c1c1c;
    --hands-light: #ece7e4;
    --hands-mid: #d9b7bd;
  }
  * { box-sizing: border-box; margin: 0; padding: 0; }
  html, body { width: 716px; height: 1200px; overflow: hidden; background: var(--backdrop); }
  body { position: relative; font-family: "Dosis", "Arial Narrow", sans-serif; }

  .window-set { position: absolute; left: 0; top: 372px; width: 716px; height: 420px; }

  .arch-half { position: absolute; top: 40px; width: 123px; height: 122px; }
  .arch-half svg { position: absolute; inset: 0; }
  .arch-half--left { left: 299px; }
  .arch-half--right { left: 426px; }
  .arch-copy {
    position: absolute; top: 33px; font-weight: 500; font-size: 15px; line-height: 20.7px;
    color: var(--forest); letter-spacing: 0.3px;
  }
  .arch-half--left .arch-copy { right: 9px; text-align: right; }
  .arch-half--right .arch-copy { left: 7px; text-align: left; }

  .pane { position: absolute; width: 123px; height: 123px; background: var(--cream); overflow: hidden; }
  .row-top { top: 166px; }
  .row-bottom { top: 292px; }
  .col-0 { left: 41px; } .col-1 { left: 172px; } .col-2 { left: 299px; }
  .col-3 { left: 426px; } .col-4 { left: 552px; }

  .wordmark { text-align: center; color: var(--forest); font-weight: 600; line-height: 1; }
  .wordmark__name { display: block; font-size: 17px; letter-spacing: 2px; }
  .wordmark__tag { display: block; font-size: 5.5px; letter-spacing: 1.6px; margin-top: 2px; }
  .wordmark__dot { display: block; width: 16px; height: 16px; border-radius: 50%; background: var(--lotus-pink); margin: 0 auto 6px; }

  .pane--name .wordmark { position: absolute; left: 0; right: 0; top: 40px; }

  .pane--pond .pond-scene { position: absolute; inset: 0; background: linear-gradient(180deg, var(--pond-mid) 0%, var(--pond-dark) 70%, #3f5c38 100%); }
  .pane--pond .pond-banner { position: absolute; inset: 0; }
  .pane--pond .wordmark { position: absolute; left: 0; right: 0; top: 30px; color: var(--white); }
  .pane--pond .wordmark__name { font-size: 14px; }
  .pane--pond .wordmark__tag { font-size: 4.5px; }

  .badge-circle { position: absolute; left: 8px; top: 8px; width: 107px; height: 107px; border-radius: 50%; background: var(--white); }
  .pane--badge .badge-circle { left: 9px; top: 9px; }
  .pane--badge .wordmark { position: absolute; left: 0; right: 0; top: 37px; }
  .leaf-accent { position: absolute; }
  .leaf-accent--top { right: 0; top: 0; width: 34px; height: 34px; background: linear-gradient(135deg, var(--blush), var(--sage)); border-bottom-left-radius: 70%; opacity: 0.85; }
  .leaf-accent--bottom { left: 0; bottom: 0; width: 22px; height: 26px; background: var(--sage); border-top-right-radius: 70%; opacity: 0.85; }

  .service-list { position: absolute; left: 0; right: 0; top: 40px; list-style: none; text-align: center; font-weight: 500; font-size: 7.6px; color: var(--ink); }
  .service-list li { width: 72px; margin: 0 auto; line-height: 12px; border-bottom: 1px dotted var(--forest); }
  .service-list li:last-child { border-bottom: none; }

  .pane--contact .hands-photo { position: absolute; left: 0; top: 0; width: 123px; height: 94px; background: linear-gradient(180deg, var(--hands-light) 0%, var(--hands-mid) 100%); border-bottom-left-radius: 40% 18%; border-bottom-right-radius: 40% 18%; }
  .contact { position: absolute; left: 0; right: 0; top: 101px; text-align: center; line-height: 8.5px; }
  .contact__phone { display: block; font-size: 7.4px; font-weight: 500; color: var(--ink); letter-spacing: 0.6px; }
  .contact__web { display: block; font-size: 6.6px; font-weight: 500; color: var(--mauve); letter-spacing: 0.5px; }
</style>
</head>
<body>
  <main class="window-set" aria-label="Fernridge Health &amp; Wellness window signage layout">
    <div class="arch-half arch-half--left">
      <svg viewBox="0 0 123 122" width="123" height="122" aria-hidden="true"><path d="M0 122 L0 112 A123 112 0 0 1 123 0 L123 122 Z" fill="var(--cream)"/></svg>
      <p class="arch-copy">DIRECT<br>HOLISTIC<br>PRIMARY<br>CARE</p>
    </div>
    <div class="arch-half arch-half--right">
      <svg viewBox="0 0 123 122" width="123" height="122" aria-hidden="true"><path d="M123 122 L123 112 A123 112 0 0 0 0 0 L0 122 Z" fill="var(--cream)"/></svg>
      <p class="arch-copy">DIRECT<br>HOLISTIC<br>PRIMARY<br>CARE</p>
    </div>

    <section class="pane pane--pond row-top col-1">
      <div class="pond-scene" role="img" aria-label="Photo of a garden pond with rocks and lily pads"></div>
      <svg class="pond-banner" viewBox="0 0 123 123" width="123" height="123" aria-hidden="true">
        <defs><linearGradient id="bannerL" x1="0" y1="0" x2="0" y2="1"><stop offset="0" stop-color="var(--forest)"/><stop offset="1" stop-color="var(--forest-deep)"/></linearGradient></defs>
        <path d="M0 0 H123 V20 C110 40 95 60 75 66 C68 70 64 76 61 78 C58 76 54 70 47 66 C27 60 12 40 0 20 Z" fill="url(#bannerL)"/>
      </svg>
      <div class="wordmark"><span class="wordmark__name">FERNRIDGE</span><span class="wordmark__tag">HEALTH &amp; WELLNESS</span></div>
    </section>

    <section class="pane pane--badge row-top col-2">
      <div class="leaf-accent leaf-accent--top" role="img" aria-label="Tropical leaf accent"></div>
      <div class="leaf-accent leaf-accent--bottom" role="img" aria-label="Tropical leaf accent"></div>
      <div class="badge-circle"></div>
      <div class="wordmark"><span class="wordmark__dot"></span><span class="wordmark__name">FERNRIDGE</span><span class="wordmark__tag">HEALTH &amp; WELLNESS</span></div>
    </section>

    <section class="pane pane--badge row-top col-3">
      <div class="leaf-accent leaf-accent--top" role="img" aria-label="Tropical leaf accent"></div>
      <div class="leaf-accent leaf-accent--bottom" role="img" aria-label="Tropical leaf accent"></div>
      <div class="badge-circle"></div>
      <div class="wordmark"><span class="wordmark__dot"></span><span class="wordmark__name">FERNRIDGE</span><span class="wordmark__tag">HEALTH &amp; WELLNESS</span></div>
    </section>

    <section class="pane pane--pond row-top col-4">
      <div class="pond-scene" role="img" aria-label="Photo of a garden pond with rocks and lily pads"></div>
      <svg class="pond-banner" viewBox="0 0 123 123" width="123" height="123" aria-hidden="true">
        <defs><linearGradient id="bannerR" x1="0" y1="0" x2="0" y2="1"><stop offset="0" stop-color="var(--forest)"/><stop offset="1" stop-color="var(--forest-deep)"/></linearGradient></defs>
        <path d="M0 0 H123 V20 C110 40 95 60 75 66 C68 70 64 76 61 78 C58 76 54 70 47 66 C27 60 12 40 0 20 Z" fill="url(#bannerR)"/>
      </svg>
      <div class="wordmark"><span class="wordmark__name">FERNRIDGE</span><span class="wordmark__tag">HEALTH &amp; WELLNESS</span></div>
    </section>

    <section class="pane pane--name row-bottom col-0">
      <div class="wordmark"><span class="wordmark__dot"></span><span class="wordmark__name">FERNRIDGE</span><span class="wordmark__tag">HEALTH &amp; WELLNESS</span></div>
    </section>

    <section class="pane pane--services row-bottom col-1">
      <div class="badge-circle"></div>
      <ul class="service-list">
        <li>Holistic Medicine</li><li>Direct Primary Care</li><li>Medical acupuncture</li><li>IV Vitamin Therapy</li>
      </ul>
    </section>

    <section class="pane pane--contact row-bottom col-2">
      <div class="hands-photo" role="img" aria-label="Photo of open hands held in a calm, meditative pose"></div>
      <p class="contact"><span class="contact__phone">318-562-7041</span><span class="contact__web">fernridgecareclinic.example</span></p>
    </section>

    <section class="pane pane--contact row-bottom col-3">
      <div class="hands-photo" role="img" aria-label="Photo of open hands held in a calm, meditative pose"></div>
      <p class="contact"><span class="contact__phone">318-562-7041</span><span class="contact__web">fernridgecareclinic.example</span></p>
    </section>

    <section class="pane pane--services row-bottom col-4">
      <div class="badge-circle"></div>
      <ul class="service-list">
        <li>Holistic Medicine</li><li>Direct Primary Care</li><li>Medical acupuncture</li><li>IV Vitamin Therapy</li>
      </ul>
    </section>
  </main>
</body>
</html>
```